Frostvale Harborline LLC

we need a business card design

Industry/Entity Type

hvac

Contact Information for Business Card

my logo

Requirements
Must have
• my logo and same colors

```html
<!DOCTYPE html>
<html lang="en">
<head>
<meta charset="utf-8">
<title>Frostvale Harborline LLC – Business Card</title>
<link href="https://fonts.googleapis.com/css2?family=Montserrat:wght@400;700&display=swap" rel="stylesheet">
<style>
  :root{
    --backdrop:#222222;
    --card-white:#ffffff;
    --brand-blue:#0063ad;
    --sky-cyan:#00b0de;
    --sun-gold:#f6b13b;
    --text-white:#ffffff;
  }
  html,body{margin:0;padding:0;width:1093px;height:1200px;overflow:hidden;background:var(--backdrop);font-family:"Montserrat",sans-serif;}
  .canvas{position:relative;width:1093px;height:1200px;}
  .card{position:absolute;left:264px;width:597px;border-radius:22px;overflow:hidden;}
  .card-front{top:225px;height:363px;background:var(--card-white);}
  .card-back{top:616px;height:366px;background:var(--brand-blue);}
  .front-bands{position:absolute;left:0;top:0;width:597px;height:363px;}
  .brand-lockup{position:absolute;display:flex;align-items:center;gap:8px;font-weight:700;white-space:nowrap;transform:translate(-50%,-50%);}
  .brand-lockup .mark{border-radius:50%;flex:none;}
  .front-brand{left:411px;top:123px;font-size:19px;color:var(--brand-blue);}
  .front-brand .mark{width:16px;height:16px;background:var(--sun-gold);}
  .back-brand{left:50%;top:50%;font-size:27px;color:var(--text-white);}
  .back-brand .mark{width:22px;height:22px;background:var(--sun-gold);}
  .contact{position:absolute;left:17px;top:233px;color:var(--text-white);}
  .contact .person-name{margin:0;font-size:21px;font-weight:700;color:var(--sun-gold);line-height:26px;white-space:nowrap;}
  .contact .person-title{margin:0 0 4px;font-size:14px;line-height:20px;}
  .contact ul{list-style:none;margin:0;padding:0;}
  .contact li{display:flex;align-items:center;gap:9px;font-size:14px;line-height:21px;white-space:nowrap;}
  .contact svg{width:16px;height:16px;flex:none;}
  .address{position:absolute;right:41px;top:321px;font-size:12.5px;line-height:18px;color:var(--text-white);white-space:nowrap;}
</style>
</head>
<body>
<div class="canvas">
  <section class="card card-front">
    <svg class="front-bands" viewBox="0 0 597 363" aria-hidden="true">
      <polygon points="0,218 171,218 309,348 0,348" fill="var(--brand-blue)"/>
      <polygon points="275,312 597,312 597,348 313,348" fill="var(--sky-cyan)"/>
    </svg>
    <div class="brand-lockup front-brand"><span class="mark"></span>Frostvale Harborline LLC</div>
    <div class="contact">
      <p class="person-name">Dana Whitfield</p>
      <p class="person-title">Managing Director</p>
      <ul>
        <li><svg viewBox="0 0 16 16"><rect x="4" y="1" width="8" height="14" rx="1.5" fill="none" stroke="var(--sun-gold)" stroke-width="1.8"/><circle cx="8" cy="12.3" r="0.9" fill="var(--sun-gold)"/></svg>+1 (555) 014-2290</li>
        <li><svg viewBox="0 0 16 16"><rect x="1.5" y="4" width="13" height="9" rx="1" fill="var(--sun-gold)"/><polyline points="1.5,4.5 8,9 14.5,4.5" fill="none" stroke="var(--brand-blue)" stroke-width="1.2"/></svg>hello@frostvalellc.com</li>
        <li><svg viewBox="0 0 16 16"><circle cx="8" cy="8" r="6.5" fill="var(--sun-gold)"/><path d="M4 5.5c2 0 2.5 1.5 1.5 3S6 12 7 13M10 3.5c-1 1.5 0 2.5 1.5 3s1.5 2 1 3" fill="none" stroke="var(--brand-blue)" stroke-width="1.2"/></svg>www.frostvalellc.com</li>
      </ul>
    </div>
    <div class="address">48 Harbor Lane, Eastby, NY 10001</div>
  </section>
  <section class="card card-back">
    <div class="brand-lockup back-brand"><span class="mark"></span>Frostvale Harborline LLC</div>
  </section>
</div>
</body>
</html>
```